Verlindo Magician

I want the business card for my business to give to people who watch that later I will be employed to show magic here is my website http://www.balsamomagicien.com/I want the interesting design , i am very opened for formal and informal, I watch a lot of design so don't stick to the common shape and form but i hope it can also be produced the thing to write on will be the same as in picture that i will upload , i also will upload the logo for you that so can be easy to useDenis CostilleMagicianMAGICIAN BALSAMO 17 rue des Tilleuls - 25000 BESANÇON contact@verlindoillusions.example tel. 0381 946 157 tel. 0674 219 503

```html
<!DOCTYPE html>
<html lang="fr">
<head>
<meta charset="utf-8">
<title>Verlindo Magician – Business Card</title>
<link rel="stylesheet" href="https://fonts.googleapis.com/css2?family=Jost:wght@300;400&display=swap">
<style>
  :root {
    --page-bg: #e7e4e0;
    --card-red: #ea2127;
    --card-dark: #1c1c1e;
    --card-dark-deep: #151517;
    --card-dark-soft: #232326;
    --card-black: #0b0b0b;
    --card-light: #fbf8f8;
    --suit-grey: #ecebeb;
    --suit-pink: #f8ecec;
    --portrait-tone: #2a2a2a;
    --portrait-tone-light: #5a5a5a;
    --text-red: #e5232b;
    --text-grey: #d4d4d6;
    --text-white: #f4f4f4;
    --ink: #111111;
  }
  html, body {
    margin: 0;
    padding: 0;
    width: 1125px;
    height: 1200px;
    overflow: hidden;
    background: var(--page-bg);
    font-family: "Jost", "Futura", sans-serif;
  }
  .canvas {
    position: relative;
    width: 1125px;
    height: 1200px;
  }
  .card {
    position: absolute;
    left: 150px;
    width: 826px;
    height: 470px;
    box-sizing: border-box;
    overflow: hidden;
  }
  .card--front {
    top: 99px;
    border: 13px solid var(--card-red);
    background: var(--card-dark);
  }
  .card--back {
    top: 630px;
    border: 13px solid var(--card-black);
    background: var(--card-light);
  }
  .suit-pattern {
    position: absolute;
    inset: 0;
  }
  .suit-pattern--dark {
    background: radial-gradient(ellipse at 50% 45%, var(--card-dark-soft) 0%, var(--card-dark) 55%, var(--card-dark-deep) 100%);
  }
  .suit-pattern--light {
    background: linear-gradient(135deg, var(--suit-grey) 0%, var(--suit-pink) 50%, var(--suit-grey) 100%);
  }
  .contact {
    position: absolute;
    left: 391px;
    top: 0;
    width: 0;
    height: 100%;
  }
  .contact__line {
    position: absolute;
    left: 0;
    transform: translate(-50%, -50%);
    white-space: nowrap;
    line-height: 1;
    font-weight: 400;
  }
  .contact__name { top: 125px; font-size: 31px; color: var(--text-red); }
  .contact__role { top: 153px; font-size: 20px; color: var(--text-grey); font-weight: 300; }
  .contact__company { top: 200px; font-size: 20.5px; color: var(--text-red); }
  .contact__address { top: 225px; font-size: 20px; color: var(--text-white); }
  .contact__email { top: 266px; font-size: 20px; color: var(--text-grey); font-weight: 300; }
  .contact__phone { top: 292px; font-size: 21px; color: var(--text-grey); font-weight: 300; letter-spacing: 0.8px; }
  .contact__web { top: 318px; font-size: 20px; color: var(--text-grey); font-weight: 300; }
  .portrait {
    position: absolute;
    left: 303px;
    top: 76px;
    width: 192px;
    height: 225px;
    border-radius: 40px 40px 16px 16px;
    background: linear-gradient(180deg, var(--portrait-tone-light) 0%, var(--portrait-tone) 100%);
  }
  .brand-name {
    position: absolute;
    left: 399px;
    top: 339px;
    transform: translate(-50%, -50%);
    font-size: 40px;
    font-weight: 300;
    letter-spacing: 1px;
    color: var(--ink);
    line-height: 1;
    white-space: nowrap;
  }
</style>
</head>
<body>
<main class="canvas">
  <section class="card card--front">
    <div class="suit-pattern suit-pattern--dark" role="img" aria-label="Subtle repeating pattern of dark card suits"></div>
    <div class="contact">
      <div class="contact__line contact__name">MARC RAVOULET</div>
      <div class="contact__line contact__role">Magician</div>
      <div class="contact__line contact__company">MAGICIAN VERLINDO</div>
      <div class="contact__line contact__address">17 rue des Tilleuls - 25000 BESANÇON</div>
      <div class="contact__line contact__email">contact@verlindoillusions.example</div>
      <div class="contact__line contact__phone">tel. 0381 946 157 tel. 0674 219 503</div>
      <div class="contact__line contact__web">www.verlindoillusions.example</div>
    </div>
  </section>

  <section class="card card--back">
    <div class="suit-pattern suit-pattern--light" role="img" aria-label="Faint repeating pattern of card suits in pale grey and pink"></div>
    <div class="portrait" role="img" aria-label="Black and white illustration of the magician in a dark jacket holding a playing card"></div>
    <div class="brand-name">VERLINDO</div>
  </section>
</main>
</body>
</html>
```